Improved Business Card, Government Contracting

We are looking to update the design of our business cards. We would like to create a template that can be used for future employees and easy to update.

Halvorsen Advisory Partners, LLC is a Service Disabled Veteran Owned Small Business with headquarters located in Tarrow Bend, OK. Our current website is www.hvadpt.com. We have contracts in KS and VA with expansion opportunities in various other states. Our primary line of work is within government contracting and providing consulting services to various organizations within the Bureau of Civic Readiness. We would like to project a professional image of our company that is consistent with the industry. Provided are previous versions of our business card template that shows our logo as well. We would like to make sure the information on the cards are easily noticeable .

Target Market(s)

Government Officials
Fellow Small Business Contractors
Large Business Contractors (ex. TQLB, Pellwick Darrow, Fenwey Marsh Colquitt)

Industry/Entity Type

Business

Contact Information for Business Card

Dale Forsyth
Office Manager
Halvorsen Advisory Partners
Ph: 555.204.7716
Email: d.forsyth@hvadpt.us
www.hvadpt.com

Requirements
Must have
• The business mailing address is:
• 48730 212th Crescent
• Tarrow Bend, OK 66091
Nice to have
• Embossed lettering

```html
<!DOCTYPE html>
<html lang="en">
<head>
<meta charset="utf-8">
<title>Halvorsen Advisory Partners – Business Card</title>
<link rel="stylesheet" href="https://fonts.googleapis.com/css2?family=Carlito:wght@400;700&display=swap">
<style>
  :root {
    --navy: #2e3192;
    --blue: #3a5aa8;
    --yellow: #fff200;
    --soft-yellow: #fff36b;
    --white: #ffffff;
    --ink: #111111;
    --backdrop: #e9e6e1;
  }
  * { margin: 0; padding: 0; box-sizing: border-box; }
  html, body {
    width: 1200px; height: 900px; overflow: hidden;
    background: var(--backdrop);
    font-family: "Carlito", "Calibri", sans-serif;
  }
  .sheet { position: relative; width: 1200px; height: 900px; }

  .card {
    position: absolute; left: 320px; width: 560px; height: 320px;
    overflow: hidden;
    box-shadow: 0 8px 22px rgba(0,0,0,.22);
  }

  /* Front */
  .card-front { top: 100px; background: var(--navy); }
  .front-brand {
    position: absolute; left: 0; right: 0; top: 0; bottom: 0;
    display: flex; align-items: center; justify-content: center; gap: 14px;
  }
  .front-brand .mark-square { width: 26px; height: 26px; background: var(--yellow); flex: none; }
  .front-brand .brand-name {
    color: var(--yellow); font-weight: 700; font-size: 36px; letter-spacing: .3px;
  }

  /* Back */
  .card-back { top: 480px; background: var(--white); }
  .top-band { position: absolute; left: 0; top: 0; width: 100%; height: 26px; background: var(--soft-yellow); }
  .bottom-band { position: absolute; left: 0; bottom: 0; width: 100%; height: 48px; background: var(--blue); }
  .side-panel {
    position: absolute; right: 0; top: 26px; width: 124px; bottom: 0;
    background: var(--blue);
    display: flex; align-items: center; justify-content: center;
    padding: 0 12px;
  }
  .side-panel .side-name {
    color: var(--soft-yellow); font-weight: 700; font-size: 19px; line-height: 1.2; text-align: center;
  }

  .back-brand {
    position: absolute; left: 32px; top: 50px;
    display: flex; align-items: center; gap: 10px;
  }
  .back-brand .mark-square { width: 16px; height: 16px; background: var(--blue); flex: none; }
  .back-brand .brand-name { color: var(--blue); font-weight: 700; font-size: 20px; }

  .person { position: absolute; left: 232px; top: 102px; }
  .person .name { color: var(--blue); font-weight: 700; font-size: 24px; line-height: 1; }
  .person .role { color: var(--ink); font-size: 18px; margin-top: 4px; }

  .contacts { position: absolute; left: 30px; top: 146px; list-style: none; }
  .contacts li {
    display: flex; align-items: center; gap: 8px;
    color: var(--ink); font-size: 18px; line-height: 25px;
  }
  .contacts svg { width: 14px; height: 14px; fill: var(--blue); flex: none; }

  .address {
    position: absolute; left: 232px; top: 194px;
    color: var(--ink); font-size: 18px; font-weight: 700; line-height: 1.25; font-style: normal;
  }
</style>
</head>
<body>
<main class="sheet">
  <section class="card card-front" aria-label="Card front">
    <div class="front-brand">
      <span class="mark-square"></span>
      <span class="brand-name">Halvorsen Advisory Partners</span>
    </div>
  </section>

  <section class="card card-back" aria-label="Card back">
    <div class="top-band"></div>
    <div class="bottom-band"></div>
    <div class="side-panel"><span class="side-name">Halvorsen Advisory Partners</span></div>

    <div class="back-brand">
      <span class="mark-square"></span>
      <span class="brand-name">Halvorsen Advisory Partners</span>
    </div>

    <div class="person">
      <p class="name">Dale Forsyth</p>
      <p class="role">Office Manager</p>
    </div>

    <ul class="contacts">
      <li>
        <svg viewBox="0 0 16 16" aria-hidden="true"><path d="M3 1h3l1.5 4-2 1.3a9 9 0 0 0 4.2 4.2L11 8.5l4 1.5v3a2 2 0 0 1-2 2A13 13 0 0 1 1 3a2 2 0 0 1 2-2z"/></svg>
        555.204.7716
      </li>
      <li>
        <svg viewBox="0 0 16 16" aria-hidden="true"><path d="M1 3h14v10H1z M1 3l7 6 7-6" stroke="#fff" stroke-width="1.2"/></svg>
        d.forsyth@hvadpt.us
      </li>
      <li>
        <svg viewBox="0 0 16 16" aria-hidden="true"><circle cx="8" cy="8" r="7"/><path d="M1 8h14M8 1c-3 4-3 10 0 14M8 1c3 4 3 10 0 14" stroke="#fff" stroke-width="1" fill="none"/></svg>
        www.hvadpt.com
      </li>
    </ul>

    <address class="address">
      48730 212th Crescent<br>
      Tarrow Bend, OK 66091
    </address>
  </section>
</main>
</body>
</html>
```